Eye catching Bottle label for pink gin targeting women 25+

We need a new label for a re-launch of our shimmering strawberry pink gin liqueur. We would like it to look premium and eye catching on the shelf. We have 2 labels we require, one for 200ml bottle (2x2 inches) and one for 500ml bottle 4x4 inches). Label must state the ml of the bottle abd that it is 18.75%Vol. Also say Shimmering Strawberry Gin Liqueur with the brand name at the top - Tallow Crane. We have a logo but it doesn't need to be used if it doesn't work with the design/colours. The gin is presented in a clear bottle and is pink and sparkly. See uploaded image for reference.

Target Market(s)

Women aged 25-45

Font styles to use
Decorative

Colors
f59296
fbd4d5
eea4c8

Requirements
Must have
• Bottle size - 500ml/200ml
• Must say 18.75% Vol
• Must have brand name - Tallow Crane
• Must have product name - Glimmering Blush Raspberry
• Must say - Gin Liqueur
Nice to have
• Some sort of floral or swirley background detail would be nice
Should not have
• Must not appeal to children

```html
<!DOCTYPE html>
<html lang="en">
<head>
<meta charset="utf-8">
<title>Tallow Crane – Glimmering Blush Raspberry Gin Liqueur Label</title>
<link rel="stylesheet" href="https://fonts.googleapis.com/css2?family=Lobster+Two:wght@700&family=Playfair+Display:wght@400;500&family=Oswald:wght@300&display=swap">
<style>
  :root {
    --page: #f6f6f6;
    --label-light: #f1e6e6;
    --label-mid: #e9cfd0;
    --blush: #fbd4d5;
    --rose: #f59296;
    --orchid: #eea4c8;
    --rose-deep: #b86a72;
    --wine: #5a2a30;
    --gold: #b88a3e;
    --gold-light: #e0bd72;
    --ink: #3b3334;
  }
  * { margin: 0; padding: 0; box-sizing: border-box; }
  html, body {
    width: 900px; height: 1200px; overflow: hidden;
    background: var(--page);
  }
  .label {
    position: absolute; left: 120px; top: 50px;
    width: 660px; height: 1100px; overflow: hidden;
    background:
      radial-gradient(ellipse 70% 30% at 75% 88%, rgba(184,106,114,.55), transparent 70%),
      radial-gradient(ellipse 60% 22% at 30% 8%, rgba(238,164,200,.35), transparent 70%),
      linear-gradient(160deg, var(--label-mid) 0%, var(--label-light) 35%, var(--label-light) 60%, var(--blush) 100%);
  }
  .swirl-band { position: absolute; inset: 0; }
  .ornament-top { position: absolute; left: 240px; top: 0; width: 420px; height: 415px; }
  .ornament-bottom { position: absolute; left: 0; top: 600px; width: 325px; height: 500px; }
  .gold-rule {
    position: absolute; height: 4px;
    background: linear-gradient(90deg, var(--gold), var(--gold-light), var(--gold));
  }
  .rule-tl-1 { left: 0; top: 87px; width: 240px; }
  .rule-tl-2 { left: 0; top: 113px; width: 240px; }
  .rule-br-1 { left: 415px; top: 955px; width: 245px; }
  .rule-br-2 { left: 415px; top: 981px; width: 245px; }
  .brand {
    position: absolute; left: 0; top: 180px; width: 660px;
    text-align: center;
    font-family: "Playfair Display", serif; font-weight: 400;
    font-size: 62px; line-height: 1.2; color: var(--ink);
  }
  .product-name {
    position: absolute;
    font-family: "Lobster Two", cursive; font-weight: 700;
    font-size: 80px; line-height: 1.2;
    color: var(--rose);
    -webkit-text-stroke: 2px var(--wine);
    text-shadow: 2px 3px 0 rgba(90,42,48,.35);
    white-space: nowrap;
  }
  .product-line-1 { top: 418px; left: 0; width: 660px; text-align: center; }
  .product-line-2 { top: 575px; left: 205px; width: 440px; text-align: center; }
  .category {
    position: absolute; left: 0; top: 748px; width: 660px; text-align: center;
    font-family: "Oswald", sans-serif; font-weight: 300;
    font-size: 78px; line-height: 1.2; letter-spacing: 1px; color: var(--gold);
  }
  .abv {
    position: absolute; right: 8px; top: 892px;
    font-family: "Playfair Display", serif; font-size: 26px; line-height: 1.2;
    font-variant-numeric: lining-nums; color: var(--ink);
  }
  .volume {
    position: absolute; left: 0; top: 1000px; width: 660px; text-align: center;
    font-family: "Playfair Display", serif; font-weight: 500;
    font-size: 54px; line-height: 1.2;
    font-variant-numeric: lining-nums; color: var(--ink);
  }
</style>
</head>
<body>
  <main class="label">
    <svg class="swirl-band" viewBox="0 0 660 1100" aria-hidden="true">
      <path d="M0 940 C180 860 380 900 660 780 L660 860 C420 980 200 930 0 1020 Z" fill="var(--rose-deep)" opacity=".28"/>
      <path d="M60 1100 C260 990 460 1040 660 960 L660 1100 Z" fill="var(--rose-deep)" opacity=".3"/>
      <path d="M0 120 C200 60 420 40 660 0 L660 40 C420 80 220 110 0 170 Z" fill="var(--orchid)" opacity=".25"/>
      <circle cx="470" cy="1040" r="26" fill="none" stroke="var(--wine)" stroke-width="6" opacity=".7"/>
      <circle cx="140" cy="180" r="6" fill="#fff" opacity=".8"/>
      <circle cx="600" cy="820" r="8" fill="#fff" opacity=".8"/>
      <circle cx="560" cy="1000" r="10" fill="#fff" opacity=".7"/>
    </svg>
    <div class="ornament-top" role="img" aria-label="Gold swirling filigree ornament"
         style="background: radial-gradient(ellipse at 75% 35%, rgba(184,138,62,.28), transparent 65%);"></div>
    <div class="ornament-bottom" role="img" aria-label="Gold swirling filigree ornament"
         style="background: radial-gradient(ellipse at 25% 55%, rgba(184,138,62,.28), transparent 65%);"></div>

    <div class="gold-rule rule-tl-1"></div>
    <div class="gold-rule rule-tl-2"></div>
    <div class="gold-rule rule-br-1"></div>
    <div class="gold-rule rule-br-2"></div>

    <p class="brand">Tallow<br>Crane</p>
    <h1 class="product-name product-line-1">Glimmering Blush</h1>
    <h1 class="product-name product-line-2">Raspberry</h1>
    <p class="category">GIN LIQUEUR</p>
    <p class="abv">18.75%Vol</p>
    <p class="volume">200ml</p>
  </main>
</body>
</html>
```